BrindleStaffing Business Card Design

We are a staffing company finding positions for dedicated nurses and physicians.

Target Market(s)

Business Professionals

Industry/Entity Type

Staffing

Contact Information for Business Card

Gordon Pratley
Chairman
417 39th Avenue South
SAINT PETERSBURG FL 33712
813-555-4172 Mobile
813-555-8036 Fax
gpratley@brindlestaffing.com
www.brindlestaffing.com

Font styles to use
Sans Serif

Colors
fbee3e
f04a50
f37122

Requirements
Must have
• Logo Attached, see colors below. We'd like to see Yellow, Orange and Red.

```html
<!DOCTYPE html>
<html lang="en">
<head>
<meta charset="utf-8">
<title>BrindleStaffing Business Card</title>
<link rel="stylesheet" href="https://fonts.googleapis.com/css2?family=Poppins:wght@600&family=Open+Sans:wght@400;600&family=Nunito+Sans:wght@400;800&display=swap">
<style>
  :root {
    --red: #f04a50;
    --orange: #f37122;
    --yellow: #fbee3e;
    --ink: #222222;
    --card: #ffffff;
    --cross: #fef8d4;
    --stage-light: #8f8f93;
    --stage-dark: #3f3e40;
  }
  * { margin: 0; padding: 0; box-sizing: border-box; }
  html, body { width: 1200px; height: 1135px; overflow: hidden; }
  body {
    position: relative;
    background: radial-gradient(ellipse at 50% 45%, var(--stage-light) 0%, #6c6b6e 45%, var(--stage-dark) 100%);
    font-family: "Open Sans", sans-serif;
    color: var(--ink);
  }
  .card {
    position: absolute;
    width: 720px;
    height: 411px;
    background: var(--card);
    border-radius: 40px;
    overflow: hidden;
    border: 1px solid #d8d8d8;
  }
  .card--front { left: 388px; top: 109px; }
  .card--back { left: 96px; top: 580px; }

  .brand-name {
    position: absolute;
    font-family: "Poppins", sans-serif;
    font-weight: 600;
    color: var(--red);
    letter-spacing: -1px;
    line-height: 1.2;
    white-space: nowrap;
    display: flex;
    align-items: center;
  }
  .brand-name .dot {
    display: inline-block;
    border-radius: 50%;
    background: var(--yellow);
    box-shadow: inset 0 0 0 2px var(--orange);
  }
  .card--front .brand-name { left: 54px; top: 46px; font-size: 47px; gap: 12px; }
  .card--front .brand-name .dot { width: 22px; height: 22px; }

  .person { position: absolute; left: 56px; top: 136px; font-family: "Nunito Sans", sans-serif; }
  .person-name { font-weight: 800; font-size: 22px; color: var(--red); line-height: 28px; }
  .person-title { font-weight: 400; font-size: 20px; color: var(--orange); line-height: 28px; }

  .address { position: absolute; left: 56px; top: 214px; font-size: 17px; line-height: 24px; }
  .contact { position: absolute; display: flex; align-items: center; gap: 9px; font-size: 17px; line-height: 24px; }
  .contact--mobile { left: 56px; top: 282px; }
  .contact--fax { left: 290px; top: 282px; }
  .contact--email { left: 56px; top: 316px; }
  .contact svg { width: 18px; height: 18px; flex: none; }
  .contact .label { color: var(--orange); font-size: 14px; font-weight: 600; }

  .footer-bands { position: absolute; left: 0; bottom: 0; width: 720px; height: 56px; }
  .footer-url {
    position: absolute; left: 57px; top: 361px;
    color: #fff; font-size: 17px; letter-spacing: 3.6px; line-height: 24px;
  }

  .cross-bar { position: absolute; background: var(--cross); }
  .cross-bar--vertical { left: 290px; top: 0; width: 165px; height: 411px; }
  .cross-bar--horizontal { left: 167px; top: 125px; width: 412px; height: 164px; }
  .card--back .brand-name { left: 108px; top: 150px; font-size: 60px; gap: 14px; }
  .card--back .brand-name .dot { width: 26px; height: 26px; }
  .back-url {
    position: absolute; left: 0; width: 720px; top: 252px; text-align: center;
    font-size: 23px; line-height: 28px; letter-spacing: 3px; color: var(--ink);
  }
  .back-url .part-a { color: var(--orange); font-weight: 600; }
  .back-url .part-b { color: var(--red); font-weight: 600; }
</style>
</head>
<body>

<section class="card card--front" aria-label="Business card front">
  <div class="brand-name"><span class="dot"></span>BrindleStaffing</div>

  <div class="person">
    <div class="person-name">Gordon Pratley</div>
    <div class="person-title">Chairman</div>
  </div>

  <div class="address">417 39th Avenue South<br>Saint Petersburg FL 33712</div>

  <div class="contact contact--mobile">
    <svg viewBox="0 0 18 18" aria-hidden="true">
      <circle cx="9" cy="9" r="8" fill="none" stroke="var(--orange)" stroke-width="1.6"/>
      <path d="M6.2 4.8c-.8.9-1 2.4-.1 4.3.9 2 2.4 3.6 4.2 4.2.9.3 1.6.1 2-.4l-1.3-1.8-1.2.5c-.9-.4-1.8-1.5-2.2-2.6l.9-.9L7.6 4.3z" fill="var(--orange)"/>
    </svg>
    <span>813-555-4172 <span class="label">Mobile</span></span>
  </div>
  <div class="contact contact--fax">
    <svg viewBox="0 0 18 18" aria-hidden="true">
      <rect x="4" y="2" width="10" height="5" fill="none" stroke="var(--orange)" stroke-width="1.5"/>
      <rect x="1.5" y="7" width="15" height="7" rx="1.5" fill="var(--orange)"/>
      <rect x="4.5" y="11.5" width="9" height="4.5" fill="#fff" stroke="var(--orange)" stroke-width="1.3"/>
    </svg>
    <span>813-555-8036 <span class="label">Fax</span></span>
  </div>
  <div class="contact contact--email">
    <svg viewBox="0 0 18 18" aria-hidden="true">
      <path d="M1.5 7.5 9 2.8l7.5 4.7v7.7h-15z" fill="var(--orange)"/>
      <path d="M3.5 7.8 9 11l5.5-3.2" fill="none" stroke="#fff" stroke-width="1.5"/>
    </svg>
    <span>gpratley@brindlestaffing.com</span>
  </div>

  <svg class="footer-bands" viewBox="0 0 720 56" preserveAspectRatio="none" aria-hidden="true">
    <rect x="0" y="0" width="720" height="56" fill="var(--red)"/>
    <path d="M0 0 H485 C470 4 465 26 448 30 H0 Z" fill="var(--orange)"/>
  </svg>
  <div class="footer-url">www.brindlestaffing.com</div>
</section>

<section class="card card--back" aria-label="Business card back">
  <div class="cross-bar cross-bar--vertical"></div>
  <div class="cross-bar cross-bar--horizontal"></div>
  <div class="brand-name"><span class="dot"></span>BrindleStaffing</div>
  <div class="back-url">www.<span class="part-a">brindle</span><span class="part-b">staffing</span>.com</div>
</section>

</body>
</html>
```